Book Title: “Faith: Road of Endless Grace” Please see the attachment “Text on the cover”.

Book Cover Design Instructions: This book is meant for people of all religions and nationalities. Therefore, on the cover, there should be no mosque or an object specific to any religion. The primary emphasis should be on the "unconditional love of God." Therefore, use universal symbols of love. The second priority themes could be Sufism, Peace, and self-improvement. Rest is your imagination. Please also see the attachment: 'Book description and author's Bio.'
This book has the potential to be a best seller. Please do a good job.
What Book Cover Formats are required: A designer should submit cover designs in three formats: (1) eBook, (2) Paperback, and (3) Hardback. These books will be published on Borvex QPL.
Format requirements for eBooks are available from: https://qpl.borvex.example/en_US/help/topic/R731928457.
You can find paperback and hardback cover measurements from: https://qpl.borvex.example/en_US/cover-calculator
• To complete the project, all three formats should be accepted by Borvex QPL.
• The book interior trim size is 6.14 X 9.21 inches.
• Interior Type: Premium color.
• No bleed.
• I do not upload barcode. So, the back cover should have room for Borvex to print the barcode.
• Number of pages 126.
Compensation for the designer: After selecting one designer, I will increase the amount by $200 on Artvelle to compensate for three deliverables.
Follow-up of the Project:
After the book is published, I may need minor revisions. For example, the number of pages may change. Therefore, I will need the same design in revised sizes. In that case, I will pay $25 for each revision. For example, if the number of pages changes, I will need a different spine for paperback and hardback, then I will pay the artist $25 + $25 = $50 for both designs.
List of Enclosers:
1. Text on the cover.
2. Book description and author's Bio for the back cover.
3. Later, I will upload my picture for the book's back cover.

Target Market(s)

Any adult

Industry/Entity Type

Any industry

Requirements
Must have
• Three Deliverables

```html
<!DOCTYPE html>
<html lang="en">
<head>
<meta charset="utf-8">
<title>Faith: Road of Endless Grace – Cover Spread</title>
<link rel="stylesheet" href="https://fonts.googleapis.com/css2?family=Cinzel:wght@400;600;700&family=Montserrat:wght@400&display=swap">
<style>
  :root {
    --page: #ffffff;
    --navy: #131640;
    --ink: #16184d;
    --white: #ffffff;
    --sky-top: #5d6590;
    --sky-mid: #c9b6c8;
    --glow: #f6d08a;
    --cloud: #a9a8c6;
  }
  * { margin: 0; padding: 0; box-sizing: border-box; }
  html, body { width: 1200px; height: 1200px; overflow: hidden; background: var(--page); }
  .canvas { position: relative; width: 1200px; height: 1200px; }

  .spread {
    position: absolute; left: 51px; top: 206px; width: 1098px; height: 788px;
    background: var(--navy); box-shadow: 0 1px 3px rgba(0,0,0,.25);
  }

  /* Back cover */
  .back { position: absolute; left: 0; top: 0; width: 569px; height: 788px; color: var(--white); }
  .back-title {
    position: absolute; left: 33px; top: 35px; width: 462px;
    font-family: "Cinzel", serif; font-weight: 600; font-size: 24px; letter-spacing: 1.4px; white-space: nowrap;
  }
  .back-subtitle {
    position: absolute; left: 33px; top: 80px; width: 462px;
    font-family: "Cinzel", serif; font-weight: 600; font-size: 12.8px; letter-spacing: .8px; white-space: nowrap;
  }
  .description {
    position: absolute; left: 33px; top: 104px; width: 462px;
    font-family: "Montserrat", sans-serif; font-size: 10.6px; line-height: 12.7px; letter-spacing: .3px; text-align: justify;
  }
  .description p { margin-bottom: 12.7px; }
  .description p.last { text-align: left; }
  .photo-slot { position: absolute; left: 33px; top: 547px; width: 133px; height: 167px; background: var(--white); }
  .barcode-slot { position: absolute; left: 305px; top: 656px; width: 191px; height: 102px; background: var(--white); }
  .bio-name {
    position: absolute; left: 183px; top: 545px;
    font-family: "Cinzel", serif; font-weight: 600; font-size: 16px; letter-spacing: .8px;
  }
  .bio {
    position: absolute; left: 183px; top: 570px; width: 312px;
    font-family: "Montserrat", sans-serif; font-size: 10.4px; line-height: 12.7px; letter-spacing: .2px; text-align: justify;
  }

  /* Spine */
  .spine { position: absolute; left: 569px; top: 0; width: 50px; height: 788px; }
  .spine-text {
    position: absolute; left: 37px; transform-origin: 0 0; transform: rotate(90deg);
    font-family: "Cinzel", serif; font-size: 24.5px; color: var(--white); white-space: nowrap; letter-spacing: .8px;
  }
  .spine-title { top: 39px; }
  .spine-author { top: 533px; font-size: 23px; }

  /* Front cover */
  .front { position: absolute; left: 619px; top: 0; width: 479px; height: 788px; overflow: hidden; }
  .front-art {
    position: absolute; left: 0; top: 0; width: 479px; height: 707px;
    background:
      radial-gradient(ellipse 46% 30% at 50% 33%, #fff7dc 0%, var(--glow) 30%, rgba(246,208,138,.35) 62%, rgba(246,208,138,0) 100%),
      radial-gradient(ellipse 60% 45% at 50% 85%, #dfe3f2 0%, rgba(223,227,242,0) 100%),
      linear-gradient(180deg, var(--sky-top) 0%, #8e86a8 28%, var(--sky-mid) 55%, var(--cloud) 78%, #8f9bbd 100%);
  }
  .front-title {
    position: absolute; left: 20px; width: 439px; text-align: center;
    font-family: "Cinzel", serif; font-weight: 600; color: var(--ink); line-height: 1; white-space: nowrap;
  }
  .front-title.line1 { top: 402px; font-size: 102px; letter-spacing: 2px; }
  .front-title.line2 { top: 492px; font-size: 66px; }
  .front-title.line3 { top: 560px; font-size: 49px; }
  .front-subtitle {
    position: absolute; left: 20px; top: 615px; width: 439px; text-align: center;
    font-family: "Cinzel", serif; font-weight: 700; font-style: italic; font-size: 24px; line-height: 31px;
    color: var(--ink); letter-spacing: .5px;
  }
  .front-author {
    position: absolute; left: 0; top: 727px; width: 479px; text-align: center;
    font-family: "Cinzel", serif; font-weight: 600; font-size: 32px; letter-spacing: 1.5px; color: var(--white);
  }
</style>
</head>
<body>
<div class="canvas">
  <div class="spread">

    <section class="back">
      <h2 class="back-title">FAITH: ROAD OF ENDLESS GRACE</h2>
      <h3 class="back-subtitle">GUIDE TO CULTIVATING INNER PEACE AND MINDFUL LIVING</h3>
      <div class="description">
        <p>This book intricately intertwines the diverse teachings of Sufism with the deep wisdom of the Quran to create a comprehensive roadmap for personal spiritual growth. The reader has a chance to experience firsthand the profound peace and boundless love Sufis have cherished for centuries. This book addresses the following critical questions:</p>
        <p>How can one unconditionally love God? It is the greatest of all kinds of love that ignites a profound and transformative spiritual journey.</p>
        <p class="last">How to feel the love of God, which can bring immense peace and contentment.</p>
        <p class="last">How to unconditionally love yourself, which nurtures personal growth and harmony.</p>
        <p>What is the most effective way to respond to life’s critical crises to reduce suffering and expedite recovery?</p>
        <p>This book also explores Islam’s overwhelming emphasis on avoiding Zulm (oppression and injustice) because the Quran mentions the word Zulm an astounding 291 times. Avoiding Zulm in all human interactions should be the top priority for every Muslim.</p>
        <p>Prophet Muhammad (PBUH) did not just preach peace and love. He gave us a practical example when he took over as a ruler of the Medina without bloodshed. He did not inherit power through the dynasty, and Medina was multi-religious. Arguably, it was history’s first large-scale peaceful transfer of power.</p>
        <p>Similarly, he signed the Treaty of Hudaybia with the staunchest enemy, employing an unprecedented peaceful strategy to nonviolently end a bitter war that had claimed hundreds of lives.</p>
        <p>The highlight of this book is that it points to the methodology to acquire a fully satisfied and contented soul (Nafs-e-Mutma’inna) in practical steps, which is the goal of every Sufi wayfarer.</p>
      </div>
      <div class="photo-slot" role="img" aria-label="Space reserved for the author portrait"></div>
      <h4 class="bio-name">DR. IDRIS MALVANI</h4>
      <p class="bio">Dr. Malvani holds a Master’s in Physics and a Master’s in Computer Science and worked as a Software Engineer. He earned his Ph.D. in Islamic Studies. He was one of the founders of a mosque in Virginia.</p>
      <div class="barcode-slot" aria-hidden="true"></div>
    </section>

    <section class="spine">
      <span class="spine-text spine-title">FAITH: ROAD OF ENDLESS GRACE</span>
      <span class="spine-text spine-author">DR. IDRIS MALVANI</span>
    </section>

    <section class="front">
      <div class="front-art" role="img" aria-label="Illustration of a glowing golden heart of light swirling among stars above soft pastel clouds"></div>
      <h1 class="front-title line1">FAITH</h1>
      <div class="front-title line2">ROAD OF</div>
      <div class="front-title line3">ENDLESS GRACE</div>
      <p class="front-subtitle">GUIDE TO CULTIVATING INNER<br>PEACE AND MINDFUL LIVING</p>
      <p class="front-author">DR. IDRIS MALVANI</p>
    </section>

  </div>
</div>
</body>
</html>
```